Bluecrest Learning Corps by graduating students from college in two years

Based on the logo design, create stationary and business cards for
Dr. Venrel T Oskamp, CEO, (703) 482-1736
and Marisa Deltoft, Respresentative, (301) 647-2208
Address: 4719 Pellham Court, Larkmoor Springs, VA 22147
Incorporate elelments of the logo

Target Market(s)

USA

Font styles to use
Other font styles liked:
• match with the logo type style

```html
<!DOCTYPE html>
<html lang="en">
<head>
<meta charset="utf-8">
<title>Bluecrest Learning Corps — Letterhead</title>
<link href="https://fonts.googleapis.com/css2?family=Crimson+Text:wght@400;600&family=Lato:wght@400;700&family=Mr+Dafoe&display=swap" rel="stylesheet">
<style>
  :root {
    --navy: #1c2456;
    --gold: #f4c12f;
    --paper: #ffffff;
    --backdrop: #cbcbcb;
    --ink: #111111;
    --body-ink: #6a6a6a;
    --muted: #555555;
  }
  * { margin: 0; padding: 0; box-sizing: border-box; }
  html, body { width: 1200px; height: 840px; overflow: hidden; }
  body { background: var(--backdrop); position: relative; font-family: "Lato", sans-serif; }

  .letterhead {
    position: absolute; top: 96px; width: 495px; height: 648px;
    background: var(--paper); overflow: hidden;
    box-shadow: 0 6px 14px rgba(0,0,0,0.25);
  }
  .letterhead--first { left: 86px; }
  .letterhead--second { left: 619px; }

  .band { position: absolute; left: 0; width: 495px; }
  .band--top { top: 0; height: 120px; }
  .band--bottom { bottom: 0; height: 120px; }

  .seal {
    position: absolute; left: 41px; top: 18px; width: 84px; height: 84px;
    border-radius: 50%; background: var(--paper);
    display: flex; align-items: center; justify-content: center; text-align: center;
    font-family: "Crimson Text", serif; font-weight: 600; color: var(--navy);
    font-size: 9px; line-height: 1.1; padding: 12px;
  }

  .masthead {
    position: absolute; left: 238px; top: 31px;
    font-family: "Crimson Text", serif; color: var(--navy);
    display: flex;
  }
  .masthead__org { font-size: 7.6px; line-height: 11px; padding-right: 8px; border-right: 1px solid var(--navy); }
  .masthead__org .caps { font-weight: 600; text-transform: uppercase; }
  .masthead__org .addr { color: var(--ink); font-size: 8px; line-height: 11.5px; }
  .masthead__people { padding-left: 8px; font-size: 8px; line-height: 12px; }
  .masthead__people .person { font-weight: 600; font-size: 9px; }
  .masthead__people .phone { color: var(--ink); display: flex; align-items: center; gap: 3px; }
  .masthead__people svg { width: 7px; height: 7px; fill: var(--navy); }

  .recipient { position: absolute; left: 52px; top: 174px; color: var(--ink); }
  .recipient__name { font-size: 10px; font-weight: 400; }
  .recipient__role { font-size: 7px; font-weight: 700; margin-top: 2px; }
  .date { position: absolute; right: 52px; top: 186px; font-size: 7px; color: var(--body-ink); }

  .letter-body {
    position: absolute; left: 52px; top: 220px; width: 391px;
    font-size: 6.9px; line-height: 11.45px; color: var(--body-ink); text-align: justify;
  }
  .letter-body p + p { margin-top: 11.45px; }

  .signature {
    position: absolute; left: 53px; top: 480px;
    font-family: "Mr Dafoe", cursive; font-size: 20px; color: var(--ink);
  }
  .sender { position: absolute; left: 52px; top: 523px; }
  .sender__name { font-size: 9.6px; font-weight: 700; color: var(--ink); }
  .sender__role { font-size: 7px; font-weight: 700; color: var(--muted); margin-top: 3px; }

  .page-number {
    position: absolute; right: 46px; bottom: 28px;
    font-family: "Crimson Text", serif; font-size: 8px; color: var(--paper);
  }
</style>
</head>
<body>

<!-- Page one -->
<div class="letterhead letterhead--first">
  <svg class="band band--top" viewBox="0 0 495 120" aria-hidden="true">
    <path d="M0 0 H274 C180 20 80 45 0 72 Z" fill="var(--navy)"/>
    <path d="M0 80 C90 48 190 20 285 0 H303 C200 22 100 56 0 102 Z" fill="var(--gold)"/>
  </svg>
  <div class="seal">Bluecrest Learning Corps</div>
  <div class="masthead">
    <div class="masthead__org">
      <div class="caps">Bluecrest Learning Corps</div>
      <div class="caps">2- Year Pathway</div>
      <div class="addr">4719 Pellham Court</div>
      <div class="addr">Larkmoor Springs, VA 22147</div>
    </div>
    <div class="masthead__people">
      <div class="person">Dr. Venrel T Oskamp, CEO</div>
      <div class="phone"><svg viewBox="0 0 10 10"><path d="M1 3 Q5 0 9 3 L8 4.5 L6.5 4 L6.5 3.2 Q5 2.6 3.5 3.2 L3.5 4 L2 4.5 Z M2.5 5 H7.5 L9 9 H1 Z"/></svg>(703) 482-1736</div>
      <div class="person">Marisa Deltoft, Respresentative</div>
      <div class="phone"><svg viewBox="0 0 10 10"><path d="M1 3 Q5 0 9 3 L8 4.5 L6.5 4 L6.5 3.2 Q5 2.6 3.5 3.2 L3.5 4 L2 4.5 Z M2.5 5 H7.5 L9 9 H1 Z"/></svg>(301) 647-2208</div>
    </div>
  </div>

  <div class="recipient">
    <div class="recipient__name">Dear. Mrs Leona Marsh Pryde</div>
    <div class="recipient__role">Chief Director</div>
  </div>
  <div class="date">Date: 24-february-2025</div>

  <div class="letter-body">
    <p>Lorem ipsum dolor sit amet, consectetur adipiscing elit, sed do eiusmod tempor incididunt ut labore et dolore magna aliqua. Sollicitudin ac orci phasellus egestas tellus rutrum tellus. Euismod elementum nisi quis eleifend quam adipiscing vitae proin sagittis. Egestas sed tempus urna et pharetra pharetra. Quis blandit turpis cursus in hac habitasse. Sed velit dignissim sodales ut eu. Ac auctor augue mauris augue neque. In arcu cursus euismod quis viverra nibh cras pulvinar mattis. Libero justo laoreet sit amet. Felis eget nunc lobortis mattis aliquam faucibus purus in. Pulvinar etiam non quam lacus suspendisse faucibus. Odio tempor orci dapibus ultrices. Velit dignissim sodales ut eu sem integer vitae justo. Fermentum et sollicitudin ac orci phasellus egestas. Pharetra vel turpis nunc eget lorem dolor sed. Sed turpis tincidunt id aliquet risus feugiat in ante. Mus mauris vitae ultricies leo integer malesuada nunc vel. Rhoncus urna neque viverra justo nec ultrices dui. Ut placerat orci nulla pellentesque dignissim enim sit amet.</p>
    <p>Bibendum arcu vitae elementum curabitur vitae nunc. Nunc pulvinar sapien et ligula ullamcorper malesuada. At elementum eu facilisis sed. Erat pellentesque adipiscing commodo elit at imperdiet dui accumsan sit. Nunc scelerisque viverra mauris in aliquam sem fringilla. In vitae turpis massa sed. Volutpat ac tincidunt vitae semper quis lectus nulla at. Massa placerat duis ultricies lacus sed turpis. Dui vivamus arcu felis bibendum ut tristique et egestas. Blandit aliquam etiam erat velit scelerisque in dictum non consectetur. Id neque aliquam vestibulum morbi blandit cursus risus at. Sed egestas egestas fringilla phasellus faucibus scelerisque eleifend donec. Ornare quam viverra orci sagittis eu volutpat odio facilisis. Volutpat sed cras ornare arcu dui vivamus arcu. Interdum consectetur libero id faucibus nisl.</p>
    <p>Viverra mauris in aliquam sem. Mattis molestie a iaculis at erat pellentesque adipiscing commodo elit. Sit amet volutpat consequat mauris nunc. Aliquam nulla facilisi cras fermentum. Sed turpis tincidunt id aliquet risus feugiat. Augue neque gravida in fermentum et sollicitudin ac orci.</p>
  </div>

  <div class="signature">Calder renwick ashby</div>
  <div class="sender">
    <div class="sender__name">Calder Renwick Ashby</div>
    <div class="sender__role">Chief Director</div>
  </div>

  <svg class="band band--bottom" viewBox="0 0 495 120" aria-hidden="true">
    <path d="M495 19 C390 75 300 108 204 120 H227 C320 110 400 85 495 32 Z" fill="var(--gold)"/>
    <path d="M495 39 C400 85 320 110 234 120 H495 Z" fill="var(--navy)"/>
  </svg>
</div>

<!-- Page two -->
<div class="letterhead letterhead--second">
  <svg class="band band--top" viewBox="0 0 495 120" aria-hidden="true">
    <path d="M0 0 H274 C180 20 80 45 0 72 Z" fill="var(--navy)"/>
    <path d="M0 80 C90 48 190 20 285 0 H303 C200 22 100 56 0 102 Z" fill="var(--gold)"/>
  </svg>
  <div class="seal">Bluecrest Learning Corps</div>
  <div class="masthead">
    <div class="masthead__org">
      <div class="caps">Bluecrest Learning Corps</div>
      <div class="caps">2- Year Pathway</div>
      <div class="addr">4719 Pellham Court</div>
      <div class="addr">Larkmoor Springs, VA 22147</div>
    </div>
    <div class="masthead__people">
      <div class="person">Dr. Venrel T Oskamp, CEO</div>
      <div class="phone"><svg viewBox="0 0 10 10"><path d="M1 3 Q5 0 9 3 L8 4.5 L6.5 4 L6.5 3.2 Q5 2.6 3.5 3.2 L3.5 4 L2 4.5 Z M2.5 5 H7.5 L9 9 H1 Z"/></svg>(703) 482-1736</div>
      <div class="person">Marisa Deltoft, Respresentative</div>
      <div class="phone"><svg viewBox="0 0 10 10"><path d="M1 3 Q5 0 9 3 L8 4.5 L6.5 4 L6.5 3.2 Q5 2.6 3.5 3.2 L3.5 4 L2 4.5 Z M2.5 5 H7.5 L9 9 H1 Z"/></svg>(301) 647-2208</div>
    </div>
  </div>

  <div class="recipient">
    <div class="recipient__name">Dear. Mrs Leona Marsh Pryde</div>
    <div class="recipient__role">Chief Director</div>
  </div>
  <div class="date">Date: 24-february-2025</div>

  <div class="letter-body">
    <p>Lorem ipsum dolor sit amet, consectetur adipiscing elit, sed do eiusmod tempor incididunt ut labore et dolore magna aliqua. Sollicitudin ac orci phasellus egestas tellus rutrum tellus. Euismod elementum nisi quis eleifend quam adipiscing vitae proin sagittis. Egestas sed tempus urna et pharetra pharetra. Quis blandit turpis cursus in hac habitasse. Sed velit dignissim sodales ut eu. Ac auctor augue mauris augue neque. In arcu cursus euismod quis viverra nibh cras pulvinar mattis. Libero justo laoreet sit amet. Felis eget nunc lobortis mattis aliquam faucibus purus in. Pulvinar etiam non quam lacus suspendisse faucibus. Odio tempor orci dapibus ultrices. Velit dignissim sodales ut eu sem integer vitae justo. Fermentum et sollicitudin ac orci phasellus egestas. Pharetra vel turpis nunc eget lorem dolor sed. Sed turpis tincidunt id aliquet risus feugiat in ante. Mus mauris vitae ultricies leo integer malesuada nunc vel. Rhoncus urna neque viverra justo nec ultrices dui. Ut placerat orci nulla pellentesque dignissim enim sit amet.</p>
    <p>Bibendum arcu vitae elementum curabitur vitae nunc. Nunc pulvinar sapien et ligula ullamcorper malesuada. At elementum eu facilisis sed. Erat pellentesque adipiscing commodo elit at imperdiet dui accumsan sit. Nunc scelerisque viverra mauris in aliquam sem fringilla. In vitae turpis massa sed. Volutpat ac tincidunt vitae semper quis lectus nulla at. Massa placerat duis ultricies lacus sed turpis. Dui vivamus arcu felis bibendum ut tristique et egestas. Blandit aliquam etiam erat velit scelerisque in dictum non consectetur. Id neque aliquam vestibulum morbi blandit cursus risus at. Sed egestas egestas fringilla phasellus faucibus scelerisque eleifend donec. Ornare quam viverra orci sagittis eu volutpat odio facilisis. Volutpat sed cras ornare arcu dui vivamus arcu. Interdum consectetur libero id faucibus nisl.</p>
    <p>Viverra mauris in aliquam sem. Mattis molestie a iaculis at erat pellentesque adipiscing commodo elit. Sit amet volutpat consequat mauris nunc. Aliquam nulla facilisi cras fermentum. Sed turpis tincidunt id aliquet risus feugiat. Augue neque gravida in fermentum et sollicitudin ac orci.</p>
  </div>

  <div class="signature">Calder renwick ashby</div>
  <div class="sender">
    <div class="sender__name">Calder Renwick Ashby</div>
    <div class="sender__role">Chief Director</div>
  </div>

  <svg class="band band--bottom" viewBox="0 0 495 120" aria-hidden="true">
    <path d="M495 19 C390 75 300 108 204 120 H227 C320 110 400 85 495 32 Z" fill="var(--gold)"/>
    <path d="M495 39 C400 85 320 110 234 120 H495 Z" fill="var(--navy)"/>
  </svg>
  <div class="page-number">1</div>
</div>

</body>
</html>
```